TA BRAMLEY BUSINESS CARD DESIGN PROJECT

We need to utilize our logo that was expertly created on PixelHarbor and now need to match this with a business card design.

```html
<!DOCTYPE html>
<html lang="en">
<head>
<meta charset="UTF-8">
<title>TA Bramley Business Card</title>
<link rel="stylesheet" href="https://fonts.googleapis.com/css2?family=Montserrat:wght@400;500;700;800&display=swap">
<style>
  :root {
    --brand-blue: #1157b0;
    --card-black: #141414;
    --paper-white: #ffffff;
    --backdrop: #e4e5e8;
    --card-radius: 22px;
  }
  * { margin: 0; padding: 0; box-sizing: border-box; }
  html, body {
    width: 1200px;
    height: 900px;
    overflow: hidden;
    background: var(--backdrop);
    font-family: "Montserrat", sans-serif;
  }
  .stage {
    position: relative;
    width: 1200px;
    height: 900px;
  }
  .card {
    position: absolute;
    left: 250px;
    width: 700px;
    height: 400px;
    border-radius: var(--card-radius);
    overflow: hidden;
    box-shadow: 0 10px 28px rgba(0,0,0,0.18);
  }
  .card-front {
    top: 30px;
    background: var(--brand-blue);
    display: flex;
    align-items: center;
    justify-content: center;
  }
  .front-wordmark {
    color: var(--paper-white);
    font-weight: 800;
    font-size: 68px;
    letter-spacing: 6px;
  }
  .card-back {
    top: 470px;
    background: var(--card-black);
  }
  .back-shapes {
    position: absolute;
    inset: 0;
  }
  .back-wordmark {
    position: absolute;
    left: 48px;
    top: 56px;
    color: var(--paper-white);
    font-weight: 800;
    font-size: 38px;
    letter-spacing: 3px;
  }
  .identity {
    position: absolute;
    left: 56px;
    top: 262px;
    white-space: nowrap;
  }
  .person-name {
    color: var(--brand-blue);
    font-weight: 700;
    font-size: 22px;
    letter-spacing: 0.5px;
  }
  .person-role {
    color: var(--paper-white);
    font-weight: 500;
    font-size: 17px;
    margin-top: 2px;
  }
  .contact-list {
    position: absolute;
    left: 56px;
    top: 322px;
    list-style: none;
  }
  .contact-item {
    display: flex;
    align-items: center;
    gap: 10px;
    color: var(--paper-white);
    font-size: 15px;
    line-height: 22px;
  }
  .contact-icon { width: 13px; height: 13px; flex: none; }
  .address {
    position: absolute;
    right: 48px;
    bottom: 44px;
    color: var(--paper-white);
    font-size: 16px;
    font-style: normal;
    line-height: 22px;
    text-align: right;
  }
</style>
</head>
<body>
<main class="stage">
  <section class="card card-front">
    <span class="front-wordmark">TA BRAMLEY</span>
  </section>

  <section class="card card-back">
    <svg class="back-shapes" viewBox="0 0 700 400" width="700" height="400" aria-hidden="true">
      <rect class="blue-field" x="0" y="0" width="700" height="400" fill="var(--brand-blue)"/>
      <path class="wave-stripe" d="M0,248 C200,228 300,165 420,70 C500,8 600,-2 700,6" fill="none" stroke="var(--card-black)" stroke-width="6"/>
      <path class="dark-field" d="M0,268 C200,248 300,185 420,90 C500,28 600,18 700,26 L700,400 L0,400 Z" fill="var(--card-black)"/>
      <line class="divider-line" x1="312" y1="278" x2="652" y2="278" stroke="var(--brand-blue)" stroke-width="1.5"/>
    </svg>

    <span class="back-wordmark">TA BRAMLEY</span>

    <div class="identity">
      <p class="person-name">DANIEL HARTWELL</p>
      <p class="person-role">Managing Director</p>
    </div>

    <ul class="contact-list">
      <li class="contact-item">
        <svg class="contact-icon" viewBox="0 0 16 16"><path d="M3 1l3 3-2 2c1 2 3 4 5 5l2-2 3 3-2 3C6 14 2 10 1 3z" fill="var(--brand-blue)"/></svg>
        770 555 0148
      </li>
      <li class="contact-item">
        <svg class="contact-icon" viewBox="0 0 16 16"><rect x="1" y="3" width="14" height="10" fill="var(--brand-blue)"/><path d="M1 3l7 6 7-6" fill="none" stroke="var(--card-black)" stroke-width="1.4"/></svg>
        info@tabramley.com
      </li>
      <li class="contact-item">
        <svg class="contact-icon" viewBox="0 0 16 16"><circle cx="8" cy="8" r="7" fill="var(--brand-blue)"/><path d="M1 8h14M8 1c-3 4-3 10 0 14M8 1c3 4 3 10 0 14" fill="none" stroke="var(--card-black)" stroke-width="1"/></svg>
        www.tabramley.com
      </li>
    </ul>

    <address class="address">418 Larkspur Lane NE<br>Marietta, GA 30062</address>
  </section>
</main>
</body>
</html>
```